Water ATM Card

Need a design for water ATM cards. Size of card is 3.375 x 2.125 inch
On the Front include the Cedar hollow Logo.
Bottom right corner should have Price $100
On the Back
This card is to be used to access water refills at any Cedar Hollow Water Vending Machines.
Please contact (869) 418 2930 or (869) 534 1276 or email clearflowbox@mailvista.example for any assistance or recharging of card.

```html
<!DOCTYPE html>
<html lang="en">
<head>
<meta charset="utf-8">
<title>Cedar Hollow Water Card</title>
<link rel="stylesheet" href="https://fonts.googleapis.com/css2?family=Montserrat:wght@400;500;700&display=swap">
<style>
  :root {
    --stage: #1c1c1c;
    --card-white: #ffffff;
    --brand-blue: #2456a4;
    --brand-green: #34a548;
    --ink: #1e1e1e;
    --back-top: #2f7fc0;
    --back-bottom: #2e3d8e;
    --back-name: #5a76c0;
    --back-note: #ffffff;
  }
  html, body {
    margin: 0;
    width: 1200px;
    height: 1059px;
    overflow: hidden;
    background: var(--stage);
    font-family: "Montserrat", sans-serif;
  }
  .card {
    position: absolute;
    left: 255px;
    width: 690px;
    height: 394px;
    border-radius: 22px;
    overflow: hidden;
  }
  .card-front { top: 87px; background: var(--card-white); }
  .card-back {
    top: 546px;
    background: linear-gradient(160deg, var(--back-top) 0%, var(--back-bottom) 100%);
  }

  /* Front */
  .brand {
    position: absolute;
    left: 40px;
    width: 284px;
    top: 196px;
    text-align: center;
  }
  .brand-name {
    margin: 0;
    font-weight: 700;
    font-size: 23px;
    letter-spacing: 0.5px;
    color: var(--brand-blue);
  }
  .brand-tagline {
    margin: 2px 0 0;
    font-weight: 500;
    font-size: 14px;
    color: var(--brand-blue);
  }
  .divider {
    position: absolute;
    left: 332px;
    top: 119px;
    width: 1.5px;
    height: 157px;
    background: var(--brand-blue);
  }
  .holder {
    position: absolute;
    left: 345px;
    top: 117px;
  }
  .holder-name {
    margin: 0;
    font-weight: 700;
    font-size: 22px;
    color: var(--brand-blue);
    letter-spacing: 0.3px;
  }
  .holder-role {
    margin: 2px 0 0;
    font-size: 14px;
    color: var(--ink);
  }
  .contacts {
    position: absolute;
    left: 345px;
    top: 185px;
    margin: 0;
    padding: 0;
    list-style: none;
    font-size: 14.5px;
    color: var(--ink);
  }
  .contacts li {
    display: flex;
    align-items: center;
    height: 24px;
  }
  .contacts li:nth-child(2) { margin-top: 4px; }
  .contacts svg {
    width: 14px;
    height: 14px;
    margin-right: 8px;
    fill: var(--brand-blue);
  }
  .price {
    position: absolute;
    right: 47px;
    top: 330px;
    margin: 0;
    font-weight: 700;
    font-size: 19px;
    color: var(--brand-green);
  }
  .front-band {
    position: absolute;
    left: 0;
    bottom: 0;
    width: 690px;
    height: 15px;
  }

  /* Back */
  .back-pattern {
    position: absolute;
    inset: 0;
  }
  .back-brand {
    position: absolute;
    left: 0;
    right: 0;
    top: 205px;
    text-align: center;
  }
  .back-brand-name {
    margin: 0;
    font-weight: 700;
    font-size: 33px;
    line-height: 1.15;
    letter-spacing: 1.5px;
    color: var(--back-name);
  }
  .back-brand-tagline {
    margin: 0;
    font-weight: 500;
    font-size: 22px;
    line-height: 1.15;
    color: var(--back-name);
  }
  .back-note {
    position: absolute;
    left: 40px;
    right: 40px;
    top: 298px;
    margin: 0;
    text-align: center;
    font-size: 13px;
    line-height: 1.45;
    color: var(--back-note);
  }
</style>
</head>
<body>
  <section class="card card-front">
    <div class="brand">
      <p class="brand-name">CEDAR HOLLOW</p>
      <p class="brand-tagline">Purified Spring Water</p>
    </div>
    <div class="divider"></div>
    <div class="holder">
      <p class="holder-name">DANIEL REYES</p>
      <p class="holder-role">OWER</p>
    </div>
    <ul class="contacts">
      <li>
        <svg viewBox="0 0 24 24"><path d="M6.6 10.8a15 15 0 0 0 6.6 6.6l2.2-2.2a1 1 0 0 1 1-.25 11.4 11.4 0 0 0 3.6.57 1 1 0 0 1 1 1V20a1 1 0 0 1-1 1A17 17 0 0 1 3 4a1 1 0 0 1 1-1h3.5a1 1 0 0 1 1 1c0 1.25.2 2.45.57 3.57a1 1 0 0 1-.25 1z"/></svg>
        (869) 418 2930
      </li>
      <li>
        <svg viewBox="0 0 24 24"><path d="M7 1h10a2 2 0 0 1 2 2v18a2 2 0 0 1-2 2H7a2 2 0 0 1-2-2V3a2 2 0 0 1 2-2zm0 3v14h10V4zm5 15.2a1.2 1.2 0 1 0 0 2.4 1.2 1.2 0 0 0 0-2.4z"/></svg>
        (869) 534 1276
      </li>
      <li>
        <svg viewBox="0 0 24 24"><path d="M2 5h20v2l-10 6L2 7zm0 4 10 6 10-6v10H2z"/></svg>
        clearflowbox@mailvista.example
      </li>
      <li>
        <svg viewBox="0 0 24 24"><path d="M12 2a10 10 0 1 0 0 20 10 10 0 0 0 0-20zm-1 17.9A8 8 0 0 1 4.1 10l4.9 5v1a2 2 0 0 0 2 2zm6.9-2.5A2 2 0 0 0 16 16h-1v-3a1 1 0 0 0-1-1H8v-2h2a1 1 0 0 0 1-1V7h2a2 2 0 0 0 2-2v-.4a8 8 0 0 1 2.9 12.8z"/></svg>
        www.cedarhollowwater.example
      </li>
    </ul>
    <p class="price">Price $100</p>
    <svg class="front-band" viewBox="0 0 690 15" preserveAspectRatio="none">
      <polygon points="0,0 332,0 346,15 0,15" fill="var(--brand-blue)"/>
      <polygon points="342,0 690,0 690,15 357,15" fill="var(--brand-green)"/>
    </svg>
  </section>

  <section class="card card-back">
    <div class="back-pattern" role="img" aria-label="Repeating tonal pattern of the brand symbol across the card, fading from dark blue on the left to light blue on the right"></div>
    <div class="back-brand">
      <p class="back-brand-name">CEDAR HOLLOW</p>
      <p class="back-brand-tagline">Purified Spring Water</p>
    </div>
    <p class="back-note">This card is to be used to access water refills at any Cedar Hollow Water Vending Machines.<br>Please contact (869) 418 2930 or (869) 534 1276 or email clearflowbox@mailvista.example<br>for any assistance or recharging of card.</p>
  </section>
</body>
</html>
```